Business Card Design Project

We have recently completed CraftHive projects for a new logo and wesbite.
We now require new business cards.
We hand out very little printed material to clients as all information is online. When we do hand out something, like a business card, we want it to have real impact and make a statement about the quality and professionalism of our company.
We have an idea of what we want our card to look like but we want a designer to make sure they have impact and look great.
Our requirements are…
Size: 85mm X 55mm - Landscape
Front of card: Logo plus the following contact information.
Dennis Marlow
Operations Manager
Phone +44(0) 1632 xxx xxx
Mobile +44(0) 7700 xxx xxx
Email denmo@korvantix.example
Address 17 Pellick Row, Aberdeen AB12 9QZ
Website www.korvantix.example
How you layout the front of the card is up to you, we would like to see some different ideas. Attached are two versions of our logo that may be used.
Back of card: We would like this to be simple but again have impact. Our current thought is to have the logo or just the large W design from the logo in white against a dark background, perhaps made up from the dark green in the logo.
The logos are attached so you can see the colours in them but the dark ones are..
Dark Blue = C:88, M:55, Y:44, K:28
Dark Green = C:87, M:53, Y:50, K:50
We sometimes also use a bright orange as an accent or highlight colour…
Orange: = C:0, M:39, Y:94, K:0

```html
<!DOCTYPE html>
<html lang="en">
<head>
<meta charset="utf-8">
<title>Korvantix Business Cards</title>
<link rel="stylesheet" href="https://fonts.googleapis.com/css2?family=Open+Sans:ital,wght@0,300;0,400;0,600;0,700;0,800;1,700&display=swap">
<style>
  :root {
    --page: #e9e6e1;
    --card: #ffffff;
    --ink-dark: #1d4650;
    --ink-body: #2b3d42;
    --teal-deep: #154449;
    --teal-mid: #4d7f87;
    --teal-light: #7ea9b0;
    --mark-faint: #4f7f86;
    --label: #222222;
  }
  * { margin: 0; padding: 0; box-sizing: border-box; }
  html, body { width: 1200px; height: 788px; overflow: hidden; }
  body {
    position: relative;
    background: var(--page);
    font-family: "Open Sans", Arial, sans-serif;
    color: var(--ink-body);
  }
  .view-label {
    position: absolute;
    width: 503px;
    text-align: center;
    font-size: 21px;
    font-weight: 400;
    color: var(--label);
  }
  .card {
    position: absolute;
    width: 503px;
    height: 325px;
    border-radius: 20px;
    background: var(--card);
    overflow: hidden;
    box-shadow: 0 4px 14px rgba(0,0,0,0.25);
  }
  .col-left { left: 65px; }
  .col-right { left: 626px; }
  .row-top { top: 53px; }
  .row-bottom { top: 443px; }
  .label-top { top: 18px; }
  .label-bottom { top: 400px; }

  .swoosh { position: absolute; inset: 0; }

  .brand {
    display: flex;
    align-items: center;
    gap: 12px;
    color: var(--ink-dark);
    font-weight: 800;
    letter-spacing: 1px;
    position: absolute;
  }
  .brand-dot { border-radius: 50%; background: var(--ink-dark); flex: none; }

  .front .brand { left: 40px; top: 50px; font-size: 32px; }
  .front .brand-dot { width: 26px; height: 26px; }

  .contact { position: absolute; left: 42px; top: 150px; }
  .contact-name { font-size: 15.5px; font-weight: 700; color: var(--ink-dark); margin-bottom: 10px; }
  .contact-role { font-size: 12.5px; font-weight: 400; color: var(--ink-dark); }
  .contact-line { font-size: 12.5px; line-height: 24px; color: var(--ink-body); }
  .contact-key { font-style: italic; font-weight: 700; }

  .back-one .brand { left: 0; right: 0; justify-content: center; top: 110px; font-size: 46px; }
  .back-one .brand-dot { width: 36px; height: 36px; }
  .web {
    position: absolute; left: 0; right: 0; text-align: center;
    font-size: 17px; letter-spacing: 2.6px; color: var(--ink-dark);
  }
  .back-one .web { top: 283px; }

  .back-two { background: var(--teal-deep); }
  .back-two .brand {
    left: 0; right: 0; justify-content: center; top: 128px;
    font-size: 52px; color: var(--mark-faint);
  }
  .back-two .brand-dot { width: 42px; height: 42px; background: var(--mark-faint); }

  .back-three .brand-dot.solo {
    position: absolute; left: 211px; top: 36px; width: 80px; height: 80px;
  }
  .back-three .brand { left: 0; right: 0; justify-content: center; top: 168px; font-size: 56px; }
  .back-three .web { top: 280px; }
</style>
</head>
<body>
  <div class="view-label col-left label-top">Front</div>
  <div class="view-label col-right label-top">Back - 1</div>
  <div class="view-label col-left label-bottom">Back - 2</div>
  <div class="view-label col-right label-bottom">Back - 3</div>

  <section class="card front col-left row-top">
    <svg class="swoosh" width="503" height="325" viewBox="0 0 503 325" aria-hidden="true">
      <defs>
        <linearGradient id="bandLight" x1="0" y1="0" x2="1" y2="0">
          <stop offset="0" stop-color="#3f6f77"/>
          <stop offset="1" stop-color="#86b0b7"/>
        </linearGradient>
      </defs>
      <path d="M405,0 C500,70 520,230 398,325 L503,325 L503,0 Z" fill="url(#bandLight)"/>
      <path d="M466,118 C478,215 400,300 272,325 L398,325 C445,280 472,210 466,118 Z"
            fill="var(--teal-deep)" stroke="#ffffff" stroke-width="4"/>
    </svg>
    <div class="brand"><span class="brand-dot"></span>KORVANTIX</div>
    <div class="contact">
      <p class="contact-name">Dennis Marlow, <span class="contact-role">Operations Manager</span></p>
      <p class="contact-line"><span class="contact-key">c</span> : +44(0) 7700 xxx xxx</p>
      <p class="contact-line"><span class="contact-key">p</span> : +44(0) 1632 xxx xxx</p>
      <p class="contact-line"><span class="contact-key">e</span> : denmo@korvantix.example</p>
      <p class="contact-line"><span class="contact-key">w</span> : www.korvantix.example</p>
      <p class="contact-line"><span class="contact-key">a</span> : 17 Pellick Row, Aberdeen AB12 9QZ</p>
    </div>
  </section>

  <section class="card back-one col-right row-top">
    <div class="brand"><span class="brand-dot"></span>KORVANTIX</div>
    <p class="web">www.korvantix.example</p>
  </section>

  <section class="card back-two col-left row-bottom">
    <div class="brand"><span class="brand-dot"></span>KORVANTIX</div>
  </section>

  <section class="card back-three col-right row-bottom">
    <span class="brand-dot solo"></span>
    <div class="brand">KORVANTIX</div>
    <p class="web">www.korvantix.example</p>
  </section>
</body>
</html>
```